Business card for Luxury Portable Restroom Trailer company

We are a Luxury Portable Restroom Trailer Company Called FALCRIDGE HIRES. Based in Orange County California. We provide portable restroom trailers for events, such as, Weddings, Concerts, Charity events, Sporting events, Tournaments, Corporate events, ect. We rent and Sell the Luxury restrooms. Our colors are white, grey, and Orange. As you will see in the logo we uploaded.
There are 2 people in the company so the names and titles will change for the 3 people but card will remain the same. Here is the information for each Person: Dwight Penner CFO 555 318-0476
next Person: Leon Marchetti VP 555 318-0476
Next Person: Owen Marchetti CEO 555 318-0476
Information to include on the card: Luxury Restroom Trailers Rental and Sales. Weddings, Concerts, Charity, Sporting and Corp. Events.

```html
<!DOCTYPE html>
<html lang="en">
<head>
<meta charset="utf-8">
<title>Falcridge Hires – Business Card</title>
<link href="https://fonts.googleapis.com/css2?family=Arimo:wght@400;700&display=swap" rel="stylesheet">
<style>
  :root {
    --backdrop: #7a7a7a;
    --paper: #f4f4f5;
    --charcoal: #4f4f52;
    --ink: #47474a;
    --orange: #ea6420;
    --white: #ffffff;
  }
  * { box-sizing: border-box; margin: 0; padding: 0; }
  html, body {
    width: 1200px; height: 900px; overflow: hidden;
    background: var(--backdrop);
    font-family: "Arimo", Arial, sans-serif;
  }
  .canvas { position: relative; width: 1200px; height: 900px; }

  .card {
    position: absolute;
    width: 620px; height: 354px;
    border-radius: 22px;
  }
  .card--front {
    left: 150px; top: 80px;
    background: var(--paper);
    border-bottom: 4px solid var(--orange);
    display: flex; flex-direction: column; align-items: center;
  }
  .card--back {
    left: 430px; top: 466px;
    background: var(--charcoal);
    border-bottom: 3px solid var(--white);
  }

  .wordmark {
    display: flex; align-items: center; gap: 12px;
    font-weight: 700; letter-spacing: 1px; white-space: nowrap;
  }
  .wordmark__square { display: block; flex: none; }

  .card--front .wordmark { margin-top: 118px; font-size: 40px; color: var(--ink); }
  .card--front .wordmark__square { width: 30px; height: 30px; background: var(--orange); }

  .tagline {
    margin-top: 72px; text-align: center;
    font-size: 15px; line-height: 20px; color: var(--ink);
  }

  .card--back .wordmark {
    position: absolute; left: 46px; top: 158px;
    font-size: 27px; color: var(--white);
  }
  .card--back .wordmark__square { width: 20px; height: 20px; background: var(--orange); }

  .contact {
    position: absolute; left: 372px; top: 68px;
    color: var(--white); font-size: 14px; line-height: 18px;
  }
  .contact__name {
    color: var(--orange); font-weight: 700; font-size: 21px;
    text-transform: uppercase; line-height: 24px;
  }
  .contact__title { margin-bottom: 12px; }
  .contact__address { margin-bottom: 12px; }
  .contact__label { color: var(--orange); font-weight: 700; display: inline-block; width: 26px; }
</style>
</head>
<body>
<main class="canvas">
  <section class="card card--front" aria-label="Card front">
    <div class="wordmark"><span class="wordmark__square"></span>FALCRIDGE HIRES</div>
    <p class="tagline">
      Luxury Restroom Trailers Rental and Sales<br>
      Weddings, Concerts, Charity, Sporting and Corp Events
    </p>
  </section>

  <section class="card card--back" aria-label="Card back">
    <div class="wordmark"><span class="wordmark__square"></span>FALCRIDGE HIRES</div>
    <div class="contact">
      <p class="contact__name">Dwight Penner</p>
      <p class="contact__title">CFO</p>
      <p class="contact__address">4120 Harbor Crest Lane<br>Tustin, CA 92780</p>
      <p><span class="contact__label">P :</span>555 318-0476</p>
      <p><span class="contact__label">E :</span>name@FALCRIDGE.com</p>
      <p><span class="contact__label">W :</span>www.FALCRIDGE.com</p>
    </div>
  </section>
</main>
</body>
</html>
```